Creation of a construction/bricklaying business website

Following the template format of "Halloway 7", the following content would need to be included:
1. Landing page with 3 tiles that go to their own pages.
- Landing page to include background photo and description of services offered.
2. 3 tiles to include:
a) "Contact Us For A Free Quote or Friendly Discussion" Form (middle tile)
b) Case Studies and Testimonials
c) Certifications and Professional Membership
- Design logo to be used from previous SketchNestle project. Example of logo attached below, please access full JPG files from our account.

Target Market(s)

Prospective clients seeking construction work (bricklaying speciality)

Industry/Entity Type

Residential Construction

Coding

Coded - Design and coding required

Number of Pages Required

4 page

Font styles to use
Sans Serif

Colors

Designer to choose colors to be used in the design.

Requirements
Must have
• Following the template format of "Halloway 7", the following content would need to be included:
• 1. Landing parent page with 3 tiles that go to the 3 child pages.
• - Landing page to include background photo and description of services offered.
• 2. 3 tiles to include:
• a) "Contact Us For A Free Quote or Friendly Discussion" Form (middle tile)
• b) Case Studies and Testimonials (first tile / left side)
• c) Certifications and Professional Memberships (third tile / right side) (This should include logos of the relevant organisations being displayed. Specifically GQT and the Pillar Seal GQT).
• - Design logo to be used from previous SketchNestle project. Example of logo attached below, please access full JPG files from our account.
Nice to have
• Sleek and modern feel.
• Approachable in terms of how people can contact the company for a quote.
• Traditional pictures to give credibility and comfort around choosing this company.
Should not have
• Cheesy pictures
• Over-complicated
• Simple to use
• Easy URL domain name

```html
<!DOCTYPE html>
<html lang="en">
<head>
<meta charset="utf-8">
<title>R.T.Marlow Construction Ltd</title>
<link rel="stylesheet" href="https://fonts.googleapis.com/css2?family=Poppins:wght@400;500;600&family=Roboto:wght@400;500&family=Open+Sans:wght@400;600&display=swap">
<style>
:root{
  --blue:#1446a0;
  --blue-dark:#0f3a8a;
  --navy:#1b2a44;
  --white:#ffffff;
  --ink:#222222;
  --muted:#555555;
  --line:#dcdcdc;
  --sky:#e9f1f8;
}
*{box-sizing:border-box;margin:0;padding:0}
html,body{width:786px;height:1200px;overflow:hidden}
body{position:relative;background:var(--white);font-family:"Poppins",sans-serif;color:var(--ink)}
.hero{position:absolute;left:0;top:0;width:786px;height:396px;
  background:linear-gradient(180deg,#2a2f36 0%,#3b4048 45%,#23272d 100%)}
.hero-photo{position:absolute;inset:0;background:radial-gradient(ellipse at 60% 40%,rgba(110,118,128,.55),rgba(20,22,26,.2) 70%)}
.brand{position:absolute;left:86px;top:32px;color:var(--white);font-weight:600;font-size:21px;line-height:1}
.brand small{display:block;font-size:9.5px;font-weight:500;letter-spacing:1.4px;margin-top:4px}
.nav{position:absolute;top:46px;right:98px;display:flex;gap:20px}
.nav a{color:var(--white);text-decoration:none;font-size:11px;font-weight:500}
.hero-title{position:absolute;left:0;right:0;top:194px;text-align:center;color:var(--white);font-size:19.5px;font-weight:600;line-height:26px}
.arrow{position:absolute;top:201px;width:22px;height:22px;border-radius:50%;background:#151515;display:flex;align-items:center;justify-content:center}
.arrow.left{left:43px}.arrow.right{left:723px}
.band{position:absolute;left:0;top:396px;width:786px;height:239px;background:var(--blue)}
.services{position:absolute;left:0;top:359px;width:786px}
.service{position:absolute;width:110px;margin-left:-55px;text-align:center}
.service .ring{width:74px;height:74px;margin:0 auto;border-radius:50%;background:var(--white);border:3px solid var(--blue);box-shadow:0 0 0 1px #fff;display:flex;align-items:center;justify-content:center}
.service span{display:block;margin-top:12px;color:var(--white);font-size:9.5px;font-weight:500}
.intro{position:absolute;left:120px;width:586px;top:500px;text-align:center;color:var(--white);font-family:"Open Sans",sans-serif;font-size:10px;line-height:18.4px}
.intro p+p{margin-top:16px}
.cards{position:absolute;top:688px;left:0;width:786px}
.card{position:absolute;top:0;width:193px;height:285px;background:var(--white);box-shadow:0 0 6px rgba(0,0,0,.18);text-align:center}
.card h2{height:57px;display:flex;align-items:center;justify-content:center;font-family:"Roboto",sans-serif;font-weight:500;font-size:11.5px;line-height:17px;color:var(--ink);padding:0 6px}
.card .media{height:127px}
.card p{margin:13px 12px 0;font-family:"Open Sans",sans-serif;font-size:8.2px;line-height:14.3px;color:var(--ink)}
.btn{display:inline-block;margin-top:9px;background:var(--blue);color:var(--white);font-family:"Open Sans",sans-serif;font-weight:600;font-size:7.8px;padding:5px 8px;border-radius:2px;box-shadow:0 1px 2px rgba(0,0,0,.3)}
.m-site{background:linear-gradient(180deg,#9dc1dc,#6f8f58)}
.m-quote{background:linear-gradient(180deg,#7fa9d2,#d9e6f0)}
.m-cert{background:linear-gradient(180deg,#8d8e8c,#cfcfcc);position:relative}
.badge{position:absolute;top:14px;border-radius:2px;background:#c8152e}
.footer-bg{position:absolute;left:0;top:973px;width:786px;height:227px;background:linear-gradient(180deg,#fff,var(--sky))}
.subscribe{position:absolute;left:240px;top:1035px;width:306px;height:26px;border:1px solid var(--line);border-radius:13px;background:var(--white);overflow:hidden}
.subscribe span{position:absolute;left:15px;top:7px;font-family:"Open Sans",sans-serif;font-size:7.5px;color:#666}
.subscribe b{position:absolute;right:0;top:0;width:77px;height:26px;background:var(--blue);color:var(--white);font-size:9.5px;font-weight:600;display:flex;align-items:center;justify-content:center;border-radius:0 13px 13px 0}
.foot-links{position:absolute;left:0;right:0;top:1086px;text-align:center;font-size:8.6px;color:var(--ink)}
.copy{position:absolute;left:0;right:0;top:1109px;text-align:center;font-size:8.6px;color:var(--ink)}
.social{position:absolute;top:1136px;left:363px;display:flex;gap:9px}
.social i{width:14px;height:14px;border-radius:2px;background:var(--blue);display:block}
</style>
</head>
<body>
<header class="hero">
  <div class="hero-photo" role="img" aria-label="Night photograph of a modern office tower"></div>
  <div class="brand">R.T.Marlow<small>CONSTRUCTION LTD</small></div>
  <nav class="nav"><a href="#">HOME</a><a href="#">SERVICES</a><a href="#">ABOUT US</a><a href="#">BLOG</a><a href="#">CONTACT US</a></nav>
  <div class="arrow left"><svg width="10" height="10" viewBox="0 0 10 10"><path d="M6.5 1.5L3 5l3.5 3.5" stroke="#fff" stroke-width="1.6" fill="none"/></svg></div>
  <div class="arrow right"><svg width="10" height="10" viewBox="0 0 10 10"><path d="M3.5 1.5L7 5 3.5 8.5" stroke="#fff" stroke-width="1.6" fill="none"/></svg></div>
  <h1 class="hero-title">R.T.Marlow Construction Ltd Is A Construction<br>Company That Has Expertise And Experience<br>In The Following Areas:</h1>
</header>

<section class="band"></section>
<div class="services">
  <div class="service" style="left:124px"><div class="ring"><svg width="36" height="36" viewBox="0 0 36 36" fill="none" stroke="#1446a0" stroke-width="1.6"><path d="M8 17L18 8l10 9"/><rect x="11" y="16" width="14" height="9"/><rect x="16" y="19" width="4" height="6"/><path d="M6 29h24M9 29l-2 3M27 29l2 3"/></svg></div><span>EXTENSIONS</span></div>
  <div class="service" style="left:231px"><div class="ring"><svg width="40" height="36" viewBox="0 0 40 36" fill="none" stroke="#1446a0" stroke-width="1.6"><path d="M4 20l9-7 9 7v10H4z"/><path d="M17 14l10-8 10 8v16H22"/><rect x="10" y="24" width="5" height="6"/><path d="M26 16h5v4h-5zM26 23h5v4h-5z"/></svg></div><span>NEW HOUSES</span></div>
  <div class="service" style="left:338px"><div class="ring"><svg width="36" height="36" viewBox="0 0 36 36" fill="#1446a0"><rect x="9" y="7" width="8" height="5"/><rect x="19" y="7" width="8" height="5"/><rect x="5" y="14" width="12" height="5"/><rect x="19" y="14" width="12" height="5"/><rect x="5" y="21" width="8" height="5"/><rect x="15" y="21" width="8" height="5"/><rect x="25" y="21" width="6" height="5"/><rect x="9" y="28" width="18" height="3"/></svg></div><span>GARDEN WALLS</span></div>
  <div class="service" style="left:446px"><div class="ring"><svg width="36" height="36" viewBox="0 0 36 36" fill="none" stroke="#1446a0" stroke-width="1.6"><rect x="6" y="5" width="12" height="5"/><path d="M12 10v6h-3v14"/><rect x="22" y="8" width="8" height="22"/><path d="M22 14h8M22 20h8"/></svg></div><span>PLASTERING</span></div>
  <div class="service" style="left:552px"><div class="ring"><svg width="36" height="36" viewBox="0 0 36 36" fill="none" stroke="#1446a0" stroke-width="1.6"><rect x="5" y="10" width="14" height="6"/><rect x="5" y="18" width="10" height="6"/><rect x="9" y="26" width="12" height="5"/><path d="M27 6v8M22 22l5-8 5 8z"/></svg></div><span>BRICKWORK</span></div>
  <div class="service" style="left:660px"><div class="ring"><svg width="36" height="36" viewBox="0 0 36 36" fill="#1446a0"><path d="M4 30l8-10 6 10z"/><path d="M18 30l7-9 7 9z"/><rect x="20" y="6" width="2" height="14"/><rect x="17" y="5" width="8" height="3"/></svg></div><span>GROUNDWORKS</span></div>
</div>
<div class="intro">
  <p>We pride ourselves on attention to detail, pride in our completed project and client satisfaction. We believe in full transparency and this is reflected in the jobs we quote for you. We break down each step with both labour and materials cost so you can see exactly what you are paying for.</p>
  <p>Feel free to get in touch and we can talk through what you are looking to achieve.</p>
</div>

<div class="footer-bg"></div>
<div class="cards">
  <article class="card" style="left:86px">
    <h2>CASE STUDIES AND<br>TESTIMONIALS</h2>
    <div class="media m-site" role="img" aria-label="Builder standing on a timber roof frame"></div>
    <p>Quis autem vel eum iure reprehenderit qui in ea voluptate velit esse quam nihil molestiae consequatur, vel illum qui dolorem</p>
    <span class="btn">READ MORE</span>
  </article>
  <article class="card" style="left:301px">
    <h2>CONTACT US FOR A FREE QUOTE<br>OR FRIENDLY DISCUSSION</h2>
    <div class="media m-quote" role="img" aria-label="Site engineer holding a tablet beneath a crane"></div>
    <p>Quis autem vel eum iure reprehenderit qui in ea voluptate velit esse quam nihil molestiae consequatur, vel illum qui dolorem</p>
    <span class="btn">CONTACT US</span>
  </article>
  <article class="card" style="left:505px">
    <h2>CERTIFICATIONS AND<br>PROFESSIONAL MEMBERSHIPS</h2>
    <div class="media m-cert" role="img" aria-label="Membership badges above a desk with plans and a small tree model">
      <i class="badge" style="left:47px;width:23px;height:35px"></i>
      <i class="badge" style="left:78px;width:22px;height:32px"></i>
      <i class="badge" style="left:108px;width:70px;height:35px"></i>
    </div>
    <p>Quis autem vel eum iure reprehenderit qui in ea voluptate velit esse quam nihil molestiae consequatur, vel illum qui dolorem</p>
    <span class="btn">READ MORE</span>
  </article>
</div>

<form class="subscribe"><span>Enter your E - mail</span><b>SUBSCRIBE</b></form>
<div class="foot-links">Home &nbsp;| &nbsp;About Us &nbsp;| &nbsp;Services &nbsp;| &nbsp;Blog &nbsp;| &nbsp;Contact Us</div>
<div class="copy">© 2018 R.T.Marlow Construction Ltd. All rights reserved. Privacy Policy &nbsp;| &nbsp;Terms &amp; Conditions</div>
<div class="social" aria-label="Social links"><i></i><i></i><i></i></div>
</body>
</html>
```